Upmarket Dessert Lounge needs a Business Card Design

We are an upmarket dessert lounge needing a business card to match our image.

We want something that is simple yet beautiful, feminine, classy, sophisticated and elegant. We want it to stand out and don't mind if it is bold.

The design should include our logo and colours of red or maroon with gold highlights. We don't mind if black is used.

Marlow & Quince

Target Market(s)

For those who like to indulge or treat themselves and give in to their temptations on good quality desserts.

Industry/Entity Type

Business

Requirements
Must have
• Must include our logo and our name

Marlow & Quince

M & Q

```html
<!DOCTYPE html>
<html lang="en">
<head>
<meta charset="utf-8">
<title>Marlow &amp; Quince – Business Card</title>
<link rel="stylesheet" href="https://fonts.googleapis.com/css2?family=Open+Sans:wght@400;600;700&display=swap">
<style>
  :root {
    --backdrop: #d9d9d9;
    --card-white: #ffffff;
    --maroon: #7a1416;
    --gold: #f6d8a4;
    --ink: #3a3a3a;
    --rule: #b5b5b5;
  }
  html, body {
    margin: 0;
    padding: 0;
    overflow: hidden;
  }
  body {
    width: 956px;
    height: 1200px;
    background: var(--backdrop);
    position: relative;
    font-family: "Open Sans", Arial, sans-serif;
  }
  .card {
    position: absolute;
    width: 798px;
    height: 456px;
    border-radius: 28px;
    box-shadow: 0 6px 14px rgba(0,0,0,0.25);
  }
  .card--front {
    left: 75px;
    top: 97px;
    background: var(--card-white);
    color: var(--ink);
  }
  .card--back {
    left: 73px;
    top: 632px;
    background: var(--maroon);
  }
  .brand-name {
    position: absolute;
    left: 0;
    right: 0;
    top: 86px;
    margin: 0;
    text-align: center;
    font-weight: 600;
    font-size: 34px;
    letter-spacing: 2px;
    color: var(--maroon);
  }
  .person {
    position: absolute;
    left: 0;
    right: 0;
    top: 240px;
    margin: 0;
    text-align: center;
    font-size: 22px;
    font-weight: 400;
  }
  .person__name { font-weight: 700; }
  .contact-list {
    position: absolute;
    left: 122px;
    top: 296px;
    margin: 0;
    padding: 0;
    list-style: none;
    font-size: 18px;
    line-height: 28px;
  }
  .contact-list b { font-weight: 700; }
  .divider {
    position: absolute;
    left: 397px;
    top: 327px;
    width: 1px;
    height: 110px;
    background: var(--rule);
  }
  .address {
    position: absolute;
    left: 429px;
    top: 381px;
    margin: 0;
    font-style: normal;
    font-size: 18px;
    line-height: 27px;
  }
  .monogram {
    position: absolute;
    left: 0;
    right: 0;
    top: 168px;
    margin: 0;
    text-align: center;
    font-weight: 600;
    font-size: 96px;
    line-height: 120px;
    color: var(--gold);
  }
</style>
</head>
<body>
  <section class="card card--front">
    <h1 class="brand-name">MARLOW &amp; QUINCE</h1>
    <p class="person"><span class="person__name">Your Name -</span> Designation</p>
    <ul class="contact-list">
      <li><b>p</b> : 123-456-7890</li>
      <li><b>c</b> : 123-456-7890</li>
      <li><b>f</b> : 123-456-7890</li>
      <li><b>e</b> : name@yourwebsite.com</li>
      <li><b>w</b> : www.marlowquince.com</li>
    </ul>
    <div class="divider"></div>
    <address class="address">0000, Street Name<br>City Name, Country Code.</address>
  </section>

  <section class="card card--back">
    <p class="monogram">M &amp; Q</p>
  </section>
</body>
</html>
```